Dental Practice Website design

Design a new website for Brambleford Dental Practice.
Design should be warm, neutral in colour, with some small amount of bright colour if needed but kept to a minimum. Website should look professional, high end. Home page should be easy to navigate and simple for patients to be able to book online.
Logo in files along with some examples of websites that we like. Please ask if any further info needed.
Menu should have:
About
New Patients
Treatments
Fees
Contact Us

Industry/Entity Type

Dentistry

Number of Pages Required

4 page

Font styles to use
Sans Serif

Colors

Designer to choose colors to be used in the design.

Requirements
Must have
• Ravelle ratings badge, book online button,
Nice to have
• neutral, relaxing colours
Should not have
• harsh, bright colours!

```html
<!DOCTYPE html>
<html lang="en">
<head>
<meta charset="utf-8">
<title>Brambleford Dental Practice</title>
<link href="https://fonts.googleapis.com/css2?family=Open+Sans:wght@400;600;700&family=Roboto:wght@400;500&display=swap" rel="stylesheet">
<style>
:root{
  --green:#8fa77c;
  --brown:#b09b84;
  --brown-line:#a58f78;
  --dark:#5a4a3e;
  --ink:#3f3a36;
  --body:#55504b;
  --peach:#efcdb8;
  --cream:#f8f5ee;
  --panel:#b09d87;
  --white:#ffffff;
  --red:#e0393a;
  --footer:#f7f6f4;
}
*{box-sizing:border-box;margin:0;padding:0}
html,body{width:1200px;height:4934px;overflow:hidden}
body{font-family:"Roboto",Arial,sans-serif;color:var(--body);background:var(--white);position:relative}
h1,h2,h3,h4,.btn{font-family:"Open Sans",Arial,sans-serif}
.btn{display:inline-block;border-radius:22px;color:var(--white);font-weight:700;font-size:14px;text-align:center;letter-spacing:.3px;white-space:nowrap}
.eyebrow{color:var(--green);font-family:"Open Sans",sans-serif;font-weight:700;font-size:19px;letter-spacing:.3px}
.section-title{color:var(--ink);font-weight:700;font-size:29px;letter-spacing:.5px}

/* header */
.site-header{position:absolute;top:0;left:0;width:1200px;height:120px}
.brand{position:absolute;left:110px;top:30px;width:220px;display:flex;align-items:center;gap:10px}
.brand-mark{flex:none;width:14px;height:14px;border:2px solid #6d6660}
.brand-name{font-family:"Open Sans",sans-serif;font-weight:400;font-size:18px;color:#6d6660;line-height:1.15;white-space:nowrap}
.contact-bar{position:absolute;top:18px;left:360px;display:flex;gap:30px;font-size:13px;color:var(--dark);white-space:nowrap}
.contact-item{display:flex;align-items:center;gap:12px}
.icon-dot{flex:none;width:32px;height:32px;border-radius:50%;background:var(--dark);display:flex;align-items:center;justify-content:center}
.main-nav{position:absolute;top:64px;left:360px;display:flex;align-items:center;gap:37px;font-size:14px;color:#222;white-space:nowrap}
.main-nav .active{border-bottom:1px solid #222}
.main-nav .btn{background:var(--dark);padding:11px 21px;font-weight:600;font-size:15px}

/* hero */
.hero{position:absolute;top:120px;left:0;width:1200px;height:540px;background:linear-gradient(90deg,#d9a98b 0%,#eccbb4 45%,#f2dccc 75%,#f4e3d6 100%)}
.hero-photo{position:absolute;left:0;top:0;width:620px;height:540px;background:radial-gradient(ellipse at 45% 50%,#e2b194 0%,#c78e6c 55%,#e9c5ad 100%)}
.hero-copy{position:absolute;left:640px;top:238px;width:530px;text-align:center}
.hero-copy h1{font-size:37px;line-height:48px;color:var(--dark);font-weight:700}
.hero-copy .btn{margin-top:20px;background:var(--dark);padding:13px 19px}

/* about */
.about{position:absolute;top:660px;left:0;width:1200px;height:420px;text-align:center}
.about .eyebrow{margin-top:72px}
.about h2{margin-top:4px}
.about p{width:850px;margin:22px auto 0;font-size:14px;line-height:31px;color:#3e3a36}
.about .btn{margin-top:22px;background:var(--green);padding:12px 50px}

/* treatments */
.treatments{position:absolute;top:1080px;left:0;width:1200px;height:1805px;background:var(--cream)}
.treatments .eyebrow{position:absolute;top:55px;width:100%;text-align:center}
.treatments h2{position:absolute;top:92px;width:100%;text-align:center}
.service{position:absolute;left:0;width:1200px;height:394px}
.service-photo{position:absolute;width:380px;height:348px;border-radius:4px}
.service-frame{position:absolute;width:382px;height:350px;border:2px solid var(--brown);border-radius:4px;background:var(--brown)}
.service-text{position:absolute;width:320px}
.service-text h3{color:var(--brown-line);font-size:19px;font-weight:600;letter-spacing:.3px}
.service-text ul{list-style:none;margin-top:12px}
.service-text li{font-size:14px;line-height:29px;color:#4a4541;display:flex;align-items:center;gap:10px}
.service-text .btn{margin-top:16px;background:var(--brown);padding:11px 33px;font-size:13px}
.rule-set{position:absolute;height:295px;width:40px}
.rule-set span{position:absolute;top:20px;width:1px;height:255px;background:#cbbfb2}
.rule-set span.bold{top:0;height:295px;width:4px;background:var(--brown)}

/* team */
.team{position:absolute;top:2885px;left:0;width:1200px;height:493px;background:var(--peach)}
.team .eyebrow{position:absolute;left:112px;top:68px}
.team h2{position:absolute;left:112px;top:98px;font-size:29px;line-height:35px;color:#6b5b4e}
.team p{position:absolute;left:112px;width:490px;font-size:12.5px;line-height:26px;color:#6e5a4c}
.team .btn{position:absolute;left:112px;top:388px;background:var(--green);padding:12px 27px;font-weight:600;font-size:13px}
.team-art{position:absolute;left:650px;top:100px;width:475px;height:285px;background:linear-gradient(120deg,#c99d85,#f1e3db 60%,#e07c86);border-radius:48% 48% 40% 40%}

/* testimonials */
.testimonials{position:absolute;top:3378px;left:0;width:1200px;height:394px}
.smile-photo{position:absolute;left:0;top:0;width:598px;height:394px;background:linear-gradient(90deg,#caa487,#e6c3a8 50%,#d8ae93)}
.split-line{position:absolute;left:295px;top:0;width:3px;height:394px;background:var(--white)}
.review-panel{position:absolute;left:598px;top:0;width:602px;height:394px;background:var(--panel);color:var(--white)}
.review-panel h2{position:absolute;left:44px;top:42px;font-size:29px;font-weight:600}
.avatar{position:absolute;left:44px;top:102px;width:112px;height:112px;border-radius:50%;background:linear-gradient(#f3e7dc,#c7a790);border:4px solid var(--white)}
.review-body{position:absolute;left:186px;top:100px;width:380px}
.review-body h4{font-size:18px;font-weight:600}
.review-body p{font-size:13px;line-height:26px;margin-top:8px}
.stars{margin-top:8px;display:flex;gap:4px}
.reviewer{font-size:13px;margin-top:10px}
.ratings-badge{position:absolute;left:186px;top:304px;width:118px;height:56px;background:var(--white);border-radius:3px}
.arrows{position:absolute;left:474px;top:334px;display:flex;gap:12px}
.arrows span{width:34px;height:34px;background:var(--white);display:flex;align-items:center;justify-content:center}

/* join */
.join{position:absolute;top:3772px;left:0;width:1200px;height:388px;text-align:center}
.join .eyebrow{margin-top:81px}
.join h2{margin-top:6px}
.join p{width:980px;margin:12px auto 0;font-size:14px;line-height:25px;color:#3e3a36}
.signup{margin-top:24px;display:flex;justify-content:center;gap:16px}
.field{width:198px;height:38px;border:1.5px solid #555;border-radius:20px;display:flex;align-items:center;justify-content:space-between;padding:0 18px;font-size:11px;color:#777}
.signup .btn{background:var(--green);width:198px;height:38px;line-height:38px;font-size:14px}

/* map */
.map{position:absolute;top:4160px;left:0;width:1200px;height:430px;background:linear-gradient(135deg,#d3d3d3,#e4e4e4 50%,#cfcfcf)}
.map-card{position:absolute;left:626px;top:148px;width:240px;height:72px;background:var(--white);border-radius:4px;display:flex;align-items:center;gap:14px;padding-left:18px;font-size:13px;line-height:19px;color:#333;white-space:nowrap}
.map .btn{position:absolute;left:502px;top:367px;background:var(--red);padding:12px 34px;font-size:14px}

/* footer */
.site-footer{position:absolute;top:4590px;left:0;width:1200px;height:344px;background:var(--footer)}
.footer-brand{position:absolute;left:126px;top:70px;display:flex;align-items:center;gap:10px}
.socials{position:absolute;left:110px;top:180px;display:flex;gap:6px}
.socials span{width:28px;height:28px;border:1.5px solid #555;border-radius:50%}
.footer-col{position:absolute;top:62px}
.footer-col h4{font-size:21px;font-weight:600;color:#4a4541}
.footer-col ul{list-style:none;margin-top:16px}
.footer-col li{font-size:14.5px;line-height:31px;color:#4a4541;white-space:nowrap}
.footer-contact li{display:flex;align-items:center;gap:14px;line-height:52px;font-size:13px}
.copyright{position:absolute;top:310px;width:100%;text-align:center;font-size:13.5px;color:#555}
.footer-code{position:absolute;right:18px;top:312px;font-size:12px;color:#777}
</style>
</head>
<body>

<header class="site-header">
  <div class="brand"><span class="brand-mark"></span><span class="brand-name">Brambleford<br>Dental Practice</span></div>
  <div class="contact-bar">
    <div class="contact-item"><span class="icon-dot"><svg width="14" height="14" viewBox="0 0 24 24"><path fill="#fff" d="M6.6 10.8a15 15 0 0 0 6.6 6.6l2.2-2.2a1 1 0 0 1 1-.25 11.4 11.4 0 0 0 3.6.6 1 1 0 0 1 1 1V20a1 1 0 0 1-1 1A17 17 0 0 1 3 4a1 1 0 0 1 1-1h3.5a1 1 0 0 1 1 1c0 1.25.2 2.45.6 3.6a1 1 0 0 1-.25 1z"/></svg></span>+1 555 014 2290</div>
    <div class="contact-item"><span class="icon-dot"><svg width="14" height="12" viewBox="0 0 24 20"><path fill="#fff" d="M2 2h20v16H2z"/><path d="M2 3l10 8 10-8" stroke="#5a4a3e" stroke-width="2" fill="none"/></svg></span>hello@bramblefordsmiles.com</div>
    <div class="contact-item"><span class="icon-dot"><svg width="12" height="16" viewBox="0 0 24 32"><path fill="#fff" d="M12 0a12 12 0 0 0-12 12c0 9 12 20 12 20s12-11 12-20A12 12 0 0 0 12 0zm0 17a5 5 0 1 1 0-10 5 5 0 0 1 0 10z"/></svg></span>United States, Brambleford Dental Practice</div>
  </div>
  <nav class="main-nav">
    <span class="active">HOME</span><span>About</span><span>New Patients</span><span>Treatments</span><span>Fees</span><span>Contact Us</span>
    <span class="btn">BOOK ONLINE</span>
  </nav>
</header>

<section class="hero">
  <div class="hero-photo" role="img" aria-label="Smiling woman with long hair resting her hand on her head"></div>
  <div class="hero-copy">
    <h1>GENTLE &amp; HIGH-QUALITY DENTAL CARE IN A WARM, RELAXING SETTING.</h1>
    <span class="btn">BOOK ONLINE NOW</span>
  </div>
</section>

<section class="about">
  <div class="eyebrow">ABOUT US</div>
  <h2 class="section-title">ABOUT BRAMBLEFORD DENTAL PRACTICE</h2>
  <p>Welcome to our friendly dental practice nestled in the heart of beautiful Hollowmere, UK. Our team of dedicated dentists, hygienists and support staff are here to provide you with exceptional dental care. With a wide array of services, including general and cosmetic dentistry, orthodontics and emergency care, we're confident that we can deliver the highest quality treatment to you and your loved ones.</p>
  <span class="btn">READ MORE</span>
</section>

<section class="treatments">
  <div class="eyebrow">TREATMENTS</div>
  <h2 class="section-title">BRAMBLEFORD DENTAL PRACTICE SERVICES</h2>

  <div class="service" style="top:176px">
    <div class="rule-set" style="left:106px;top:40px"><span style="left:0"></span><span class="bold" style="left:29px"></span><span style="left:16px"></span></div>
    <div class="service-text" style="left:216px;top:88px">
      <h3>GENERAL DENTISTRY</h3>
      <ul><li><svg width="12" height="10" viewBox="0 0 12 10"><path d="M1 5l3.5 3.5L11 1" stroke="#8a8a8a" stroke-width="1.5" fill="none"/></svg>Routine Check-Ups &amp; Examinations</li><li><svg width="12" height="10" viewBox="0 0 12 10"><path d="M1 5l3.5 3.5L11 1" stroke="#8a8a8a" stroke-width="1.5" fill="none"/></svg>Dental Hygiene &amp; Cleanings</li><li><svg width="12" height="10" viewBox="0 0 12 10"><path d="M1 5l3.5 3.5L11 1" stroke="#8a8a8a" stroke-width="1.5" fill="none"/></svg>Fillings &amp; Restorations</li></ul>
      <span class="btn">READ MORE</span>
    </div>
    <div class="service-frame" style="left:711px;top:5px"></div>
    <div class="service-photo" role="img" aria-label="Patient in a dental chair with a dentist" style="left:702px;top:14px;background:linear-gradient(135deg,#cfe0e6,#f1ece6 55%,#b9c9cf)"></div>
  </div>

  <div class="service" style="top:570px">
    <div class="service-frame" style="left:116px;top:5px"></div>
    <div class="service-photo" role="img" aria-label="Dentist in a mask examining a young patient" style="left:107px;top:14px;background:linear-gradient(135deg,#d9e2ea,#f2ece8 55%,#d8a7a2)"></div>
    <div class="service-text" style="left:702px;top:88px">
      <h3>COSMETIC DENTISTRY</h3>
      <ul><li><svg width="12" height="10" viewBox="0 0 12 10"><path d="M1 5l3.5 3.5L11 1" stroke="#8a8a8a" stroke-width="1.5" fill="none"/></svg>Teeth Whitening</li><li><svg width="12" height="10" viewBox="0 0 12 10"><path d="M1 5l3.5 3.5L11 1" stroke="#8a8a8a" stroke-width="1.5" fill="none"/></svg>Composite Bonding</li><li><svg width="12" height="10" viewBox="0 0 12 10"><path d="M1 5l3.5 3.5L11 1" stroke="#8a8a8a" stroke-width="1.5" fill="none"/></svg>Veneers</li></ul>
      <span class="btn">READ MORE</span>
    </div>
    <div class="rule-set" style="left:1030px;top:40px"><span style="left:0"></span><span class="bold" style="left:10px"></span><span style="left:30px"></span></div>
  </div>

  <div class="service" style="top:964px">
    <div class="rule-set" style="left:106px;top:40px"><span style="left:0"></span><span class="bold" style="left:29px"></span><span style="left:16px"></span></div>
    <div class="service-text" style="left:216px;top:88px">
      <h3>ORTHODONTICS</h3>
      <ul><li><svg width="12" height="10" viewBox="0 0 12 10"><path d="M1 5l3.5 3.5L11 1" stroke="#8a8a8a" stroke-width="1.5" fill="none"/></svg>Traditional Braces</li><li><svg width="12" height="10" viewBox="0 0 12 10"><path d="M1 5l3.5 3.5L11 1" stroke="#8a8a8a" stroke-width="1.5" fill="none"/></svg>Clearline &amp; Clear Aligners</li><li><svg width="12" height="10" viewBox="0 0 12 10"><path d="M1 5l3.5 3.5L11 1" stroke="#8a8a8a" stroke-width="1.5" fill="none"/></svg>Retainers</li></ul>
      <span class="btn">READ MORE</span>
    </div>
    <div class="service-frame" style="left:711px;top:5px"></div>
    <div class="service-photo" role="img" aria-label="Close-up of a smile with dental braces" style="left:702px;top:14px;background:linear-gradient(135deg,#f3dfd6,#e8c3b3 55%,#c78f86)"></div>
  </div>

  <div class="service" style="top:1358px">
    <div class="service-frame" style="left:116px;top:5px"></div>
    <div class="service-photo" role="img" aria-label="Dental mirror examining a patient's open mouth" style="left:107px;top:14px;background:linear-gradient(135deg,#e5c7bb,#c48b86 50%,#d7e1ea)"></div>
    <div class="service-text" style="left:702px;top:88px">
      <h3>CHILDREN'S DENTISTRY</h3>
      <ul><li><svg width="12" height="10" viewBox="0 0 12 10"><path d="M1 5l3.5 3.5L11 1" stroke="#8a8a8a" stroke-width="1.5" fill="none"/></svg>Pediatric Check-Ups</li><li><svg width="12" height="10" viewBox="0 0 12 10"><path d="M1 5l3.5 3.5L11 1" stroke="#8a8a8a" stroke-width="1.5" fill="none"/></svg>Fluoride Treatments</li><li><svg width="12" height="10" viewBox="0 0 12 10"><path d="M1 5l3.5 3.5L11 1" stroke="#8a8a8a" stroke-width="1.5" fill="none"/></svg>Fissure Sealants</li></ul>
      <span class="btn">READ MORE</span>
    </div>
    <div class="rule-set" style="left:1030px;top:40px"><span style="left:0"></span><span class="bold" style="left:10px"></span><span style="left:30px"></span></div>
  </div>
</section>

<section class="team">
  <div class="eyebrow">OUR TEAM</div>
  <h2>COMMITTED TO YOUR COMFORT<br>AND CARE</h2>
  <p style="top:178px">We are proud to introduce our skilled and compassionate dental team, dedicated to providing high-quality care in a comfortable and welcoming environment.</p>
  <p style="top:256px">Led by our experienced dentist, our team includes knowledgeable hygienists, attentive dental assistants, and friendly reception staff—all committed to your oral health and overall well-being. Each member brings unique expertise to ensure personalized treatment tailored to your needs.</p>
  <span class="btn">MEET OUR TEAM</span>
  <div class="team-art" role="img" aria-label="Two tooth-shaped frames showing a smiling patient during a check-up and a close-up of a smile"></div>
</section>

<section class="testimonials">
  <div class="smile-photo" role="img" aria-label="Before and after teeth whitening smile comparison"></div>
  <div class="split-line"></div>
  <div class="review-panel">
    <h2>CLIENT TESTIMONIALS</h2>
    <div class="avatar" role="img" aria-label="Patient portrait"></div>
    <div class="review-body">
      <h4>Exceptional Care in a Relaxing Setting!</h4>
      <p>From the moment I walked in, I felt at ease. The staff is incredibly friendly, and the atmosphere is so calming. My cleaning was gentle yet thorough—highly recommend Brambleford Dental Practice!</p>
      <div class="stars">
        <svg width="80" height="14" viewBox="0 0 80 14"><g fill="#fff"><path id="s" d="M7 0l2 4.6 5 .4-3.8 3.2 1.2 4.8L7 10.4 2.6 13l1.2-4.8L0 5l5-.4z"/><use href="#s" x="16"/><use href="#s" x="32"/><use href="#s" x="48"/><use href="#s" x="64"/></g></svg>
      </div>
      <div class="reviewer">— Elena R.</div>
    </div>
    <div class="ratings-badge" role="img" aria-label="Ravelle ratings badge"></div>
    <div class="arrows">
      <span><svg width="10" height="16" viewBox="0 0 10 16"><path d="M8 1L2 8l6 7" stroke="#333" stroke-width="1.6" fill="none"/></svg></span>
      <span><svg width="10" height="16" viewBox="0 0 10 16"><path d="M2 1l6 7-6 7" stroke="#333" stroke-width="1.6" fill="none"/></svg></span>
    </div>
  </div>
</section>

<section class="join">
  <div class="eyebrow">JOIN OUR PRACTICE</div>
  <h2 class="section-title">A COMFORTABLE AND FRIENDLY EXPERIENCE.</h2>
  <p>If you're looking for an exceptional dental practice, we're here to help! Our team is made up of highly skilled professionals who are dedicated to ensuring that all our patients receive top-notch care in a welcoming and comfortable environment. Whether you need a routine examination or a more specialised treatment, we have all the resources to provide you with the best dental care possible.</p>
  <div class="signup">
    <div class="field">Full Name<svg width="12" height="12" viewBox="0 0 12 12"><circle cx="6" cy="3.5" r="3" fill="#444"/><path d="M0 12a6 5 0 0 1 12 0z" fill="#444"/></svg></div>
    <div class="field">Email address<svg width="12" height="10" viewBox="0 0 12 10"><rect width="12" height="10" fill="#444"/><path d="M0 1l6 4 6-4" stroke="#fff" fill="none"/></svg></div>
    <span class="btn">START NOW</span>
  </div>
</section>

<section class="map" role="img" aria-label="Street map showing the practice location">
  <div class="map-card">
    <svg width="38" height="38" viewBox="0 0 38 38"><circle cx="19" cy="19" r="19" fill="#e0393a"/><path d="M19 9a7 7 0 0 0-7 7c0 5 7 12 7 12s7-7 7-12a7 7 0 0 0-7-7zm0 10a3 3 0 1 1 0-6 3 3 0 0 1 0 6z" fill="#fff"/></svg>
    <span>United States,<br>Brambleford Dental Practice.</span>
  </div>
  <span class="btn">HOW TO FIND US</span>
</section>

<footer class="site-footer">
  <div class="footer-brand"><span class="brand-mark"></span><span class="brand-name">Brambleford<br>Dental Practice</span></div>
  <div class="socials"><span></span><span></span><span></span><span></span><span></span></div>
  <div class="footer-col" style="left:362px"><h4>Quick Links</h4><ul><li>Home</li><li>About</li><li>New Patients</li><li>Treatments</li><li>Fees</li><li>Contact Us</li></ul></div>
  <div class="footer-col" style="left:556px"><h4>Our Treatments</h4><ul><li>Preventative Care</li><li>Cosmetic Dentistry</li><li>Restorative Care</li><li>Emergency Dentistry</li></ul></div>
  <div class="footer-col footer-contact" style="left:790px"><h4>Contact Us</h4>
    <ul>
      <li><span class="icon-dot"><svg width="14" height="14" viewBox="0 0 24 24"><path fill="#fff" d="M6.6 10.8a15 15 0 0 0 6.6 6.6l2.2-2.2a1 1 0 0 1 1-.25 11.4 11.4 0 0 0 3.6.6 1 1 0 0 1 1 1V20a1 1 0 0 1-1 1A17 17 0 0 1 3 4a1 1 0 0 1 1-1h3.5a1 1 0 0 1 1 1c0 1.25.2 2.45.6 3.6a1 1 0 0 1-.25 1z"/></svg></span>+1 555 014 2290</li>
      <li><span class="icon-dot"><svg width="14" height="12" viewBox="0 0 24 20"><path fill="#fff" d="M2 2h20v16H2z"/><path d="M2 3l10 8 10-8" stroke="#5a4a3e" stroke-width="2" fill="none"/></svg></span>hello@bramblefordsmiles.com</li>
      <li><span class="icon-dot"><svg width="12" height="16" viewBox="0 0 24 32"><path fill="#fff" d="M12 0a12 12 0 0 0-12 12c0 9 12 20 12 20s12-11 12-20A12 12 0 0 0 12 0zm0 17a5 5 0 1 1 0-10 5 5 0 0 1 0 10z"/></svg></span>United States, Brambleford Dental Practice</li>
    </ul>
  </div>
  <div class="copyright">Copyright © [2025] Brambleford Dental Practice. All Rights Reserved.</div>
  <div class="footer-code">C75</div>
</footer>

</body>
</html>
```